Web Design Project

We are an IT System Integrator. We provide Korvin 450 ERP System, CRM etc. We also provide hardware, networking servicing. Please look at www.zolvantix.com.sg. They provide the same service as us. We like to redesign our web site. I will attached the color that I prefer for reference.

Our website is www.tadurk.com.sg.  It has been created about 14 years ago.  We are trying to revamp it with a new look and information.   The new website must be informative, fast.    I have attached an attachment which show the color that I prefer(brownish golden).   

Our competitor (www.zolvantix.com) is carrying the same trade as us.  They have all the informations In their website that we will like to have.  Therefore I recommend you to take a look at my competitor website and have a better   
understanding on the kind of information I would like to have for my new website.

This project is guarantee to the person with the best design.  We can have it guarantee.

Target Market(s)

Corporate and companies

Industry/Entity Type

Hardware

```html
<!DOCTYPE html>
<html lang="en">
<head>
<meta charset="utf-8">
<title>Tadurk Information System</title>
<link rel="stylesheet" href="https://fonts.googleapis.com/css2?family=Arimo:wght@400;700&family=Montserrat:wght@600;700&family=PT+Sans:wght@400;700&display=swap">
<style>
:root{
  --brown-deep:#4e3205;
  --brown:#6e4b12;
  --gold:#c9a24e;
  --gold-light:#dcb765;
  --gold-text:#b08420;
  --heading-brown:#7a5212;
  --page:#f2f1ee;
  --ink:#1c1c1c;
  --grey-text:#555;
  --white:#fff;
  --partner:#c9c9c9;
}
*{margin:0;padding:0;box-sizing:border-box}
html,body{width:856px;height:1200px;overflow:hidden}
body{position:relative;background:var(--page);font-family:"PT Sans",sans-serif;color:var(--ink)}
.abs{position:absolute}

.top-band{left:0;top:0;width:856px;height:131px;background:linear-gradient(180deg,var(--brown-deep) 0%,#7a5718 55%,#a7843a 100%)}
.top-stripe{left:0;top:131px;width:856px;height:7px;background:var(--gold-light)}

.main-nav{top:27px;left:440px;display:flex;gap:0;font-size:11px;color:var(--white)}
.main-nav a{color:var(--white);text-decoration:none}
.main-nav span.sep{margin:0 6px}
.main-nav a.current{border-bottom:1px solid var(--white);padding-bottom:2px}

.header-box{left:72px;top:49px;width:713px;height:82px;background:var(--white)}
.brand{left:20px;top:24px;display:flex;align-items:center;gap:10px}
.brand-mark{width:30px;height:30px;border-radius:50%;background:var(--gold)}
.brand-name{font-family:"PT Sans",sans-serif;font-size:14px;line-height:14px;color:var(--brown)}
.login{left:533px;top:10px;font-size:9px;color:#444}
.login label{position:absolute;white-space:nowrap}
.login .field{position:absolute;left:47px;width:121px;height:16px;border:1px solid #cfcfcf;border-radius:3px;background:#fff}
.login .check{position:absolute;left:0;top:42px;width:11px;height:11px;border:1px solid #bbb;border-radius:2px}
.login .btn{position:absolute;left:119px;top:38px;width:50px;height:15px;background:#9a7326;color:#fff;font-size:9px;text-align:center;line-height:15px;border-radius:2px}

.hero{left:72px;top:130px;width:713px;height:275px;background:linear-gradient(90deg,#dcdcdc 0%,#e6e6e6 35%,#d8d6d2 50%,#8d96a0 72%,#6c7684 100%);box-shadow:0 8px 10px -4px rgba(0,0,0,.35)}
.hero-copy{left:99px;top:218px;font-family:"Arimo",sans-serif;font-weight:700;color:var(--brown);line-height:1}
.hero-copy span{display:block;position:absolute;white-space:nowrap}
.hero-dots{left:220px;top:316px;display:flex;gap:3px}
.hero-dots i{width:11px;height:11px;border-radius:50%;background:#555}
.hero-dots i.on{background:#fff;border:2px solid #555}

.welcome{left:0;top:448px;width:856px;text-align:center;font-family:"Montserrat",sans-serif;font-weight:700;font-size:28px;color:var(--heading-brown)}
.notch{left:420px;top:487px}
.lead{left:178px;top:518px;width:500px;text-align:center;font-size:12.5px;font-weight:700;line-height:14px}
.intro{left:205px;top:557px;width:446px;text-align:center;font-size:10.5px;line-height:14.6px;color:var(--grey-text)}
.rule{top:636px;height:1px;background:#cfcfcf}
.read-more-btn{left:394px;top:625px;width:73px;height:22px;border:1px solid #bbb;border-radius:3px;background:linear-gradient(#fafafa,#e3e3e3);font-size:12px;text-align:center;line-height:20px;color:#222}

.partner{background:var(--partner)}

.feature{top:778px;width:221px;height:153px;border:1px solid #c9c9c9;border-radius:3px;background:linear-gradient(#f7f7f7,#e3e3e3);text-align:center}
.feature h3{margin-top:13px;font-family:"PT Sans",sans-serif;font-weight:400;font-size:17px;color:var(--gold-text)}
.feature p{margin:12px auto 0;width:196px;font-size:10.5px;line-height:14.6px;color:#333}
.feature a{display:block;margin-top:9px;font-size:10.5px;color:#7a5212;text-decoration:none}

.footer-band{left:0;top:972px;width:856px;height:228px;background:linear-gradient(180deg,var(--brown-deep) 0%,#5f400c 40%,#a07c33 100%)}
.footer-stripe{left:0;top:968px;width:856px;height:5px;background:#8a6a28}
.f-col{top:1004px;color:var(--white);font-size:9.5px;line-height:12px}
.f-col h4{font-family:"Arimo",sans-serif;font-weight:400;font-size:16px;color:var(--gold-light);margin-bottom:11px}
.f-col .accent{color:var(--gold-light)}
.f-col p{margin-bottom:8px}
.footer-rule{left:93px;top:1152px;width:668px;height:1px;background:rgba(255,255,255,.25)}
.footer-nav{left:93px;top:1165px;font-size:9px;color:var(--white)}
.footer-nav span.sep{margin:0 4px}
.copyright{right:95px;top:1165px;font-size:9px;color:var(--white)}
</style>
</head>
<body>
<div class="abs top-band"></div>
<div class="abs top-stripe"></div>

<nav class="abs main-nav">
  <a class="current">Home</a><span class="sep">•</span><a>Solution</a><span class="sep">•</span><a>Hardware</a><span class="sep">•</span><a>Services</a><span class="sep">•</span><a>Clients</a><span class="sep">•</span><a>About Us</a><span class="sep">•</span><a>Contact Us</a>
</nav>

<header class="abs header-box">
  <div class="abs brand">
    <div class="brand-mark"></div>
    <div class="brand-name">Tadurk<br>Information<br>System</div>
  </div>
  <form class="abs login">
    <label style="top:3px;left:0">user name</label><span class="field" style="top:0"></span>
    <label style="top:22px;left:0">password</label><span class="field" style="top:19px"></span>
    <span class="check"></span><label style="top:43px;left:16px">remember me</label>
    <span class="btn">Log in</span>
  </form>
</header>

<div class="abs hero" role="img" aria-label="Photo of a technician holding a laptop beside server racks in a data centre"></div>
<div class="abs hero-copy">
  <span style="left:0;top:0;font-size:23px">Accounting software,</span>
  <span style="left:101px;top:22px;font-size:29px">networking,</span>
  <span style="left:32px;top:50px;font-size:17.5px">hardware maintenance</span>
  <span style="left:47px;top:68px;font-size:16px;font-weight:400;color:var(--gold-text)">and consulting assistance</span>
</div>
<div class="abs hero-dots"><i></i><i></i><i class="on"></i><i></i></div>

<h1 class="abs welcome">Welcome to Tadurk Information System</h1>
<svg class="abs notch" width="16" height="8" viewBox="0 0 16 8"><polyline points="0,0 8,7 16,0" fill="none" stroke="#d6d2c8"/></svg>
<p class="abs lead">Lorem ipsum dolor sit amet, consectetur adipiscing elit. Sed id tempus enim. Etiam eros velit, rutrum in fringilla id, fermentum sit amet nulla. Nullam cursus mi ut</p>
<p class="abs intro">Aenean dapibus lorem laoreet ante pharetra ornare malesuada orci ornare. Ut volutpat ipsum ipsum, eget suscipit mauris. Sed sed nisl ac justo rutrum convallis. Fusce facilisis, nunc et viverra iaculis, arcu augue tempor ipsum, ut auctor sapien justo ac metus. Morbi adipiscing sodales condimentum. Nunc porta hendrerit turpis, nec pharetra enim interdum id.</p>
<div class="abs rule" style="left:299px;width:90px"></div>
<div class="abs rule" style="left:472px;width:90px"></div>
<div class="abs read-more-btn">Read More</div>

<div class="abs partner" style="left:193px;top:701px;width:68px;height:28px;border-radius:4px"></div>
<div class="abs partner" style="left:291px;top:701px;width:93px;height:26px;border-radius:4px"></div>
<div class="abs partner" style="left:414px;top:692px;width:44px;height:44px;border-radius:50%"></div>
<div class="abs partner" style="left:492px;top:692px;width:44px;height:44px;border-radius:4px"></div>
<div class="abs partner" style="left:580px;top:700px;width:96px;height:28px;border-radius:4px"></div>

<section class="abs feature" style="left:85px">
  <h3>Success Stories</h3>
  <p>Aenean dapibus lorem laoreet ante pharetra ornare malesuada orci ornare. Ut volutpat ipsum ipsum, eget suscipit mauris. Sed sed nisl ac justo rutrum convallis. Fusce facilisis,</p>
  <a>Read More</a>
</section>
<section class="abs feature" style="left:318px">
  <h3>Latest KORVIN</h3>
  <p>Aenean dapibus lorem laoreet ante pharetra ornare malesuada orci ornare. Ut volutpat ipsum ipsum, eget suscipit mauris. Sed sed nisl ac justo rutrum convallis. Fusce facilisis,</p>
  <a>Read More</a>
</section>
<section class="abs feature" style="left:551px">
  <h3>Service Beyond</h3>
  <p>Aenean dapibus lorem laoreet ante pharetra ornare malesuada orci ornare. Ut volutpat ipsum ipsum, eget suscipit mauris. Sed sed nisl ac justo rutrum convallis. Fusce facilisis,</p>
  <a>Read More</a>
</section>

<div class="abs footer-band"></div>
<div class="abs footer-stripe"></div>

<div class="abs f-col" style="left:93px;width:220px">
  <h4>Testimonials</h4>
  <p>" The [staff at]...Tadurk Information Systems, are friendly attentive and supportive. Any problem, regardless of time, ... "</p>
  <p style="margin-bottom:0"><span class="accent">-Group Data &amp; System Manager,<br>Quillmere Technologies Ltd</span><br>(Article featured in IT Horizon magazine, Oct 2000)</p>
</div>
<div class="abs f-col" style="left:343px;width:190px">
  <h4>Recent News</h4>
  <p><span class="accent">Aliquam bibendum pretium metus vel</span><br>Sed lacinia vulputate dolor, nec congue nunc accumsan at. Praesent leo magna,</p>
  <p><span class="accent">Praesent leo magna, imperdiet et mollis</span><br>Morbi blandit, odio dignissim laoreet bibendum, nibh sapien condimentum lectus, in</p>
</div>
<div class="abs f-col" style="left:579px;width:190px">
  <h4>Contact Us</h4>
  <p><span class="accent">Tadurk Information System Pte Ltd</span><br>18 Pelham Crescent<br># 03-41/42 Brightvale Park<br>Singapore - 561284</p>
  <p style="margin-top:14px"><span class="accent">Telephone No:</span> (065) 6391 - 5820<br><span class="accent">Facsimile No:</span> (065) 6391 - 5827</p>
</div>

<div class="abs footer-rule"></div>
<nav class="abs footer-nav">Home<span class="sep">•</span>Solution<span class="sep">•</span>Hardware<span class="sep">•</span>Services<span class="sep">•</span>Clients<span class="sep">•</span>About Us<span class="sep">•</span>Contact Us</nav>
<div class="abs copyright">© Copyright 2013. All Rights Reserved.</div>
</body>
</html>
```